Seeking funky, innovative business cards

I am looking to refresh our current business cards to something more engaging, visual and impactful. We are a management consultancy firm, see website (www.larkstone-partners.com.au). I've included our colour scheme, sample of the slides we use and our old business cards. We would like our cards to have icons. The card should display:- Name- Title- Mobile number- Address- Email address- Website - Company logo- Our purpose statement "We create the best places on earth to work"

Contact Information for Business Card

Brennan Ulfsson
Consultant
0468 927 341
Level 3, 218 Wexley Street, Melbourne 3000
brennan@larkstone-partners.com.au
www.larkstone-partners.com.au

Purpose statement "we create the best places on earth to work"
LOGO available in google images

Font styles to use
Other font styles liked:
• Open Sans Light, Bebas Neue (open to other cool foints)

Colors
ffc214
5c5c5c
f5f5f5
fefefe

Requirements
Must have
• - Name
• - Title
• - Mobile number
• - Address
• - Email address
• - Website
• - Company logo
• - Our purpose statement "We create the best places on earth to work"
Nice to have
• - Icons
• - Colour (see our colour scheme"

```html
<!DOCTYPE html>
<html lang="en">
<head>
<meta charset="utf-8">
<title>Larkstone Partners – Business Cards</title>
<link href="https://fonts.googleapis.com/css2?family=Lato:wght@400;700&display=swap" rel="stylesheet">
<style>
  :root {
    --stage: #161616;
    --card: #262626;
    --card-edge: #2e2e2e;
    --yellow: #ffc214;
    --white: #fefefe;
    --soft: #f5f5f5;
  }
  * { box-sizing: border-box; margin: 0; padding: 0; }
  html, body {
    width: 1200px; height: 900px; overflow: hidden;
    background: var(--stage);
    font-family: "Lato", Arial, sans-serif;
  }
  .stage {
    width: 1200px; height: 900px;
    display: flex; flex-direction: column;
    align-items: center; justify-content: center; gap: 36px;
  }
  .card {
    width: 680px; height: 394px;
    background: linear-gradient(135deg, var(--card) 0%, var(--card-edge) 100%);
    position: relative;
    box-shadow: 0 10px 30px rgba(0,0,0,.6);
  }

  .brand { display: flex; align-items: center; gap: 14px; }
  .brand__dot { width: 16px; height: 16px; border-radius: 50%; background: var(--yellow); flex: none; }
  .brand__name {
    color: var(--white); font-weight: 400;
    letter-spacing: -1px; line-height: 1;
  }

  .card--front .front__inner {
    position: absolute; left: 50%; top: 50%;
    transform: translate(-50%, -50%);
    display: flex; flex-direction: column; align-items: center; gap: 18px;
  }
  .card--front .brand__name { font-size: 60px; white-space: nowrap; }
  .purpose {
    color: var(--soft); font-size: 15px; letter-spacing: 3px;
    text-transform: uppercase; white-space: nowrap;
  }

  .card--back .brand {
    position: absolute; left: 44px; top: 150px;
  }
  .card--back .brand__name { font-size: 50px; width: 230px; }

  .divider {
    position: absolute; left: 352px; top: 96px;
    width: 2px; height: 206px; background: var(--yellow);
  }
  .details {
    position: absolute; left: 378px; top: 96px; right: 20px;
    color: var(--soft);
  }
  .details__name {
    color: var(--yellow); font-weight: 700; font-size: 26px;
    letter-spacing: 2.5px; text-transform: uppercase; line-height: 1.1;
  }
  .details__title { font-size: 16px; margin-top: 2px; }
  .details__address { font-size: 16px; line-height: 1.3; margin-top: 16px; }
  .contacts { list-style: none; margin-top: 14px; }
  .contacts li {
    display: flex; align-items: center; gap: 10px;
    font-size: 15px; line-height: 1.65; white-space: nowrap;
  }
  .contacts svg { width: 14px; height: 14px; flex: none; }
</style>
</head>
<body>
<main class="stage">
  <section class="card card--front" aria-label="Card front">
    <div class="front__inner">
      <div class="brand">
        <span class="brand__dot"></span>
        <span class="brand__name">Larkstone Partners</span>
      </div>
      <p class="purpose">We create the best places on earth to work</p>
    </div>
  </section>

  <section class="card card--back" aria-label="Card back">
    <div class="brand">
      <span class="brand__dot"></span>
      <span class="brand__name">Larkstone Partners</span>
    </div>
    <div class="divider"></div>
    <div class="details">
      <h1 class="details__name">Brennan Ulfsson</h1>
      <p class="details__title">Consultant</p>
      <p class="details__address">Level 3, 218 Wexley Street<br>Melbourne 3000</p>
      <ul class="contacts">
        <li>
          <svg viewBox="0 0 16 16" aria-hidden="true"><path d="M3 1.5l3 3-1.6 1.6a9 9 0 0 0 5.5 5.5L11.5 10l3 3-1.8 1.8C7 15 1 9 1.2 3.3z" fill="none" stroke="var(--yellow)" stroke-width="1.4" stroke-linejoin="round"/></svg>
          0468 927 341
        </li>
        <li>
          <svg viewBox="0 0 16 16" aria-hidden="true"><rect x="1.5" y="3.5" width="13" height="9" fill="none" stroke="var(--yellow)" stroke-width="1.4"/><path d="M1.5 3.5L8 9l6.5-5.5" fill="none" stroke="var(--yellow)" stroke-width="1.4"/></svg>
          brennan@larkstone-partners.com.au
        </li>
        <li>
          <svg viewBox="0 0 16 16" aria-hidden="true"><g fill="none" stroke="var(--yellow)" stroke-width="1.2"><circle cx="8" cy="8" r="6.5"/><ellipse cx="8" cy="8" rx="3" ry="6.5"/><path d="M1.5 8h13M2.5 4.7h11M2.5 11.3h11"/></g></svg>
          www.larkstone-partners.com.au
        </li>
      </ul>
    </div>
  </section>
</main>
</body>
</html>
```